Logo and Website Design for QR.KA Horizon - a Software Engineering and IT company

Software engineering and IT are two different disciplines - and yet inseparably linked. At QR.KA Horizon, we combine both worlds and ensure that our software solutions are not only innovative and powerful, but also integrate perfectly into existing IT landscapes. Vision stands more for imagination, so it is not neccessary something what has to do with visualisation. Please consider that the winning competitor is also instructed to make a logo for the company. So please make a suitable logo for QR.KA Horizon to which the website fits to and show it during the website creation process. A good Logo desing is important for winning the competition. The website should contain a landing page with inspiring, perhaps futuristic photos of a datacenter and lines of code. Eventuelly flewent integrated in the text. On the landing page the company should introduced with a small text (max 250 words) followed by a section with a short text to one of our products nearby a graphic visualising the architecture of the product. The menue should be on top and fixed during scrolling and consist of the menue items home, solutions, who are we and a contact button. There should be a footer for linking social media, rights and Impressum. Only as an idea not a must. The very first view on the landing page could also be the menue bar and below of it a transparent unsharp photo (e.g. datacenter, lines of code, both ;) with the company name in the center.

###############################################################

Hi Designers,

Despite your very good approaches for describing QR.KA Horizon, here a short introduction (german text) from ourself:

------
QR.KA Horizon – Ihr Partner für ganzheitliche Softwarelösungen

Die QR.KA Horizon ist ein dynamisches Unternehmen, das sich nicht nur auf die Konzeption, das Design und die Entwicklung maßgeschneiderter Software spezialisiert hat, sondern auch deren reibungslosen Betrieb sicherstellt. Mit einem Team aus erfahrenen Softwarearchitekten und IT-Professionals verbinden wir modernste Softwareentwicklung mit tiefgehendem IT-Know-how – für Lösungen, die nachhaltig, leistungsstark und zukunftssicher sind.

Software Engineering trifft IT – Perfektion in Kombination
Software Engineering und IT sind zwei unterschiedliche Disziplinen – und doch untrennbar miteinander verbunden. Wir bei QR.KA Horizon vereinen beide Welten und sorgen dafür, dass unsere Softwarelösungen nicht nur innovativ und leistungsfähig sind, sondern sich auch perfekt in bestehende IT-Landschaften integrieren.

Expertise mit Fokus auf Healthcare & komplexe IT-Umgebungen
Unsere Experten bringen jahrzehntelange Erfahrung aus dem Healthcare-Sektor mit und unterstützen IT-Abteilungen großer Kliniken in der Entwicklung und Optimierung von Softwarelösungen. Von Anwendungssoftware bis hin zu Steuerungssystemen – unsere Softwareingenieure wissen genau, worauf es ankommt.

Ganzheitlicher Ansatz – über die Software hinaus
Wir entwickeln nicht nur Software, sondern übernehmen auch die Verantwortung für deren stabile und effiziente Betriebsumgebung. Egal, ob on-premises, in der Cloud oder als SaaS-Lösung – wir kümmern uns um den kompletten Lifecycle Ihrer Anwendung.

Ihre Vision – unsere Mission.
Ob Neuentwicklung einer SaaS-Anwendung oder die Migration bestehender Lösungen in eine moderne SaaS-Umgebung – mit QR.KA Horizon haben Sie einen starken Partner an Ihrer Seite.

Lassen Sie uns gemeinsam die Zukunft Ihrer Software gestalten!
--------------

Our first solution called "Clear Record Transfer Gateway" (CLURA)
-------------------
Teilen Sie Ihre Daten sicher – ohne Kompromisse!

Sie nutzen eine relationale Datenbank (Brightcask, Tabulon Hub, Vellumdb etc.) und möchten ausgewählte Daten mit Dritten teilen – sei es für ein Data Warehouse, Business Controller, Lieferanten oder Kunden? Doch dabei sollen Datensicherheit, Integrität und Verfügbarkeit Ihrer primären Lösung in keiner Weise gefährdet werden?

Mit unserer Lösung erhalten Sie genau das: Maximalen Schutz für Ihre Anwendung bei gleichzeitigem Nutzen durch autorisierte Dritte – ganz ohne teure Lizenzkosten für eine Schattendatenbank.

Lassen Sie uns gemeinsam herausfinden, wie Sie Ihre Daten sicher und effizient nutzen können. Kontaktieren Sie uns – wir zeigen Ihnen, was möglich ist!
---------------------

Our second solution MIVO:
---------------------
MIVO – Program for a Tone Matching Instrument ist die smarte Lösung für Unternehmen, die bei Farbgenauigkeit keine Kompromisse machen. Die Software erkennt Farbabweichungen zwischen Mustern vollautomatisch, beschreibt sie verständlich und sorgt so für gleichbleibend hohe Produktqualität – schnell, visuell und präzise. Perfekt für alle, die Farbe zur Vertrauenssache machen.
-------------------------

Thanks,
Gerold

Target Market(s)

IT Professionals from any sector

Industry/Entity Type

Healthcare and other

Coding

Coded - Design and coding required

Number of Pages Required

1 page

Font styles to use
Sans Serif

Colors
0054AA
0677BA
7BADD7
CADEEF
E8F1F8
0094D4
00A9DD
6FCCEA
C7EBF8
E9F6FB
00AB8E
00BBA5
67D7C9
C6EFE9
E9F9F6

Requirements
Must have
• Please see description
Nice to have
• On the landing page the company should introduced with a small text (max 250 words) followed by a section with a short text to one of our products nearby a graphic visualising the architecture of the product. The menue should be on top and fixed during scrolling and consist of the menue items home, solutions, who are we and a contact button. There should be a footer for linking social media, rights and Impressum. Only as an idea not a must. The very first view on the landing page could also be the menue bar and below of it a transparent unsharp photo (e.g. datacenter, lines of code, both ;) with the company name in the center.
Should not have
• Please see description

```html
<!DOCTYPE html>
<html lang="en">
<head>
<meta charset="UTF-8">
<title>QR.KA Horizon – Software Engineering &amp; IT</title>
<link href="https://fonts.googleapis.com/css2?family=Poppins:ital,wght@0,400;0,500;0,600;0,700;1,400&display=swap" rel="stylesheet">
<style>
:root{
  --blue-deep:#0054AA;
  --blue:#0677BA;
  --sky:#00A9DD;
  --sky-btn:#1FA8DC;
  --sky-pale:#E5F3FA;
  --teal:#00AB8E;
  --teal-2:#1DB59C;
  --teal-light:#67D7C9;
  --ink:#1c1c1c;
  --text:#3b3b3b;
  --white:#ffffff;
  --footer:#141414;
}
*{margin:0;padding:0;box-sizing:border-box}
html,body{width:1200px;height:3983px;overflow:hidden}
body{font-family:'Poppins',sans-serif;color:var(--ink);background:var(--white)}
.page{position:relative;width:1200px;height:3983px;overflow:hidden}
.abs{position:absolute}

/* header */
.site-header{position:absolute;top:0;left:0;width:1200px;height:102px;background:var(--white);z-index:5}
.brand{position:absolute;left:74px;top:24px;display:flex;align-items:center;gap:10px}
.brand-mark{width:16px;height:16px;border-radius:50%;background:var(--teal)}
.brand-name{font-weight:600;font-size:28px;color:var(--blue-deep);line-height:1}
.nav{position:absolute;top:38px;font-size:16px;font-weight:600;color:#222}
.nav.active{color:var(--teal)}
.btn{display:flex;align-items:center;justify-content:center;border-radius:30px;color:var(--white);font-weight:600;background:linear-gradient(90deg,var(--sky-btn),#1d8fd6)}
.contact-btn{position:absolute;left:982px;top:23px;width:145px;height:58px;font-size:16px;background:var(--sky-btn)}

/* hero */
.hero{position:absolute;top:102px;left:0;width:1200px;height:561px;background:radial-gradient(ellipse at 55% 45%,#27406a 0%,#111d33 60%,#0a1221 100%)}
.hero-text{position:absolute;top:130px;width:1200px;text-align:center;color:var(--white)}
.hero-text .welcome{font-size:46px;font-weight:700;line-height:1.1}
.hero-text h1{font-size:80px;font-weight:700;line-height:1;margin-top:2px}
.hero-text p{font-size:24px;font-weight:600;line-height:1.35;width:720px;margin:14px auto 0}
.hero-btn{position:absolute;left:528px;top:372px;width:145px;height:56px;font-size:16px}
.dots{position:absolute;top:521px;left:571px;display:flex;gap:8px}
.dots span{width:10px;height:10px;border-radius:50%;background:var(--white)}
.dots span:first-child{background:var(--teal-light)}

/* headings */
.sec-title{position:absolute;font-size:42px;font-weight:400;line-height:1.2}
.sec-title b{font-weight:700;color:var(--blue-deep)}
.center{width:1200px;left:0;text-align:center}
.body-text{position:absolute;font-size:13.5px;line-height:29px;color:var(--text)}
.small-btn{position:absolute;width:152px;height:50px;font-size:15px}
.placeholder{position:absolute;border-radius:8px}

/* cards */
.card{position:absolute;top:1400px;width:329px;height:263px;background:var(--white);border-radius:14px;box-shadow:0 4px 18px rgba(0,60,110,.08);padding:24px 18px}
.card svg{display:block}
.card h3{font-size:23px;font-weight:500;line-height:1.1;margin-top:22px;color:#222}
.card.featured h3{color:var(--sky-btn)}
.card p{font-size:14.5px;line-height:26px;color:var(--text);margin-top:16px}

/* testimonial */
.quote-mark{position:absolute;left:572px;top:2470px;width:56px;height:56px;border-radius:50%;background:var(--sky-btn);color:var(--white);font-size:40px;font-weight:700;text-align:center;line-height:62px}
.quote{position:absolute;top:2542px;left:240px;width:720px;text-align:center;font-size:23px;font-style:italic;line-height:38px;color:#333}
.person{position:absolute;top:2708px;width:1200px;text-align:center}
.person strong{display:block;font-size:21px;font-weight:600;color:var(--blue-deep)}
.person span{font-size:13px;color:#555}

/* news */
.news{position:absolute;top:3035px;width:329px}
.news .thumb{height:207px;border-radius:14px}
.news h3{font-size:24px;font-weight:500;line-height:30px;color:var(--sky-btn);margin-top:20px}
.news p{font-size:14.5px;line-height:26px;color:var(--text);margin-top:14px}

/* footer */
.footer{position:absolute;top:3555px;left:0;width:1200px;height:428px;background:var(--footer);color:var(--white)}
.subscribe{position:absolute;left:74px;top:54px;font-size:41px;line-height:1.2}
.subscribe b{font-weight:700}
.email{position:absolute;left:550px;top:62px;width:388px;height:38px;border:1px solid #cfcfcf;border-radius:20px;font-size:12px;padding:11px 22px;color:#e8e8e8}
.sub-btn{position:absolute;left:950px;top:62px;width:123px;height:36px;font-size:15px;background:var(--sky-btn)}
.rule{position:absolute;left:74px;top:163px;width:1053px;height:1px;background:#3a3a3a}
.f-col{position:absolute;top:210px}
.f-col h4{font-size:18px;font-weight:500;margin-bottom:14px}
.f-col a{display:block;font-size:15px;color:#e6e6e6;text-decoration:none;line-height:34px}
.f-brand{position:absolute;left:74px;top:212px;display:flex;align-items:center;gap:10px}
.copy{position:absolute;left:74px;top:292px;font-size:12px;line-height:24px;color:#e6e6e6}
.copy a{color:var(--sky-btn);text-decoration:none}
.socials{position:absolute;left:74px;top:350px;display:flex;gap:14px;font-size:12px;color:#e6e6e6}
.socials span{display:flex;align-items:center;gap:4px}
.socials i{width:7px;height:7px;border-radius:50%;background:var(--sky-btn);display:block}
</style>
</head>
<body>
<div class="page">

<header class="site-header">
  <div class="brand"><span class="brand-mark"></span><span class="brand-name">QR.KA Horizon</span></div>
  <span class="nav active" style="left:630px">Home</span>
  <span class="nav" style="left:722px">Solutions</span>
  <span class="nav" style="left:844px">Who Are We</span>
  <a class="btn contact-btn">Contact Us</a>
</header>

<section class="hero">
  <div class="abs" style="inset:0" role="img" aria-label="Blurred photo of a data center with glowing lines of code"></div>
  <div class="hero-text">
    <div class="welcome">Welcome to</div>
    <h1>QR.KA Horizon</h1>
    <p>Excepteur sint occaecat cupidatat non proidentsunt in culpa qui officia deserunt mollit.</p>
  </div>
  <a class="btn hero-btn">Read More</a>
  <div class="dots"><span></span><span></span><span></span><span></span></div>
</section>

<svg class="abs" style="left:0;top:663px" width="1200" height="110" viewBox="0 0 1200 110">
  <polygon points="0,0 1200,0 1200,0 700,20 0,45" fill="#1f4fa3"/>
  <polygon points="165,35 1200,0 1200,30 165,65" fill="var(--teal-2)"/>
  <polygon points="780,40 1200,30 1200,100" fill="#c7e6f5"/>
</svg>

<section>
  <h2 class="sec-title" style="left:74px;top:808px">About <b>QR.KA Horizon</b></h2>
  <p class="body-text" style="left:74px;top:873px;width:560px">Sed ut perspiciatis unde omnis iste natus error sit voluptatem accusantium doloremque laudantium, totam rem aperiam, eaque ipsa quae ab illo inventore veritatis et quasi architecto beatae vitae dicta sunt explicabo. Nemo enim ipsam voluptatem quia voluptas sit aspernatur aut odit aut fugit, sed quia consequuntur magni dolores eos qui ratione voluptatem sequi nesciunt. Neque porro quisquam est, qui dolorem ipsum quia dolor sit amet, consectetur, adipisci velit, sed quia non numquam eius modi tempora .</p>
  <a class="btn small-btn" style="left:74px;top:1098px">Learn More</a>
  <div class="placeholder" style="left:660px;top:805px;width:505px;height:315px;background:linear-gradient(135deg,#eef3f6,#d9e3ea)" role="img" aria-label="Illustration of a monitor showing charts, surrounded by servers and reports"></div>
</section>

<svg class="abs" style="left:0;top:1180px" width="1200" height="660" viewBox="0 0 1200 660">
  <path d="M0,100 L600,40 C800,0 1000,-20 1120,30 C1190,60 1200,120 1200,170 L1200,520 L700,600 C500,640 200,660 60,650 C20,645 0,620 0,600 Z" fill="var(--sky-pale)"/>
  <polygon points="0,100 600,42 560,50 0,115" fill="var(--teal-2)"/>
  <path d="M0,100 L600,40 L560,55 L0,118 Z" fill="var(--teal-2)"/>
  <path d="M670,585 L1200,525 L1200,555 L700,595 Z" fill="var(--teal-2)"/>
</svg>

<section>
  <h2 class="sec-title center" style="top:1310px">Our <b>Solutions</b></h2>
  <article class="card" style="left:74px">
    <svg width="60" height="60" viewBox="0 0 60 60" fill="none" stroke="var(--sky-btn)" stroke-width="2"><rect x="8" y="6" width="44" height="50" rx="3"/><line x1="16" y1="16" x2="44" y2="16"/><line x1="16" y1="26" x2="44" y2="26"/><line x1="16" y1="36" x2="44" y2="36"/><line x1="16" y1="46" x2="44" y2="46"/><line x1="30" y1="6" x2="30" y2="56"/></svg>
    <h3>Excepteur Sint<br>Occaecat</h3>
    <p>Excepteur sint occaecat cupidatat non proident, sunt in culpa qui officia deserunt error sit..</p>
  </article>
  <article class="card featured" style="left:436px">
    <svg width="70" height="60" viewBox="0 0 70 60" fill="none" stroke="var(--blue-deep)" stroke-width="2"><rect x="4" y="10" width="62" height="40" rx="3"/><path d="M18 24l-6 6 6 6M30 24l6 6-6 6"/><line x1="44" y1="22" x2="58" y2="22"/><line x1="44" y1="30" x2="58" y2="30"/><line x1="44" y1="38" x2="58" y2="38"/><line x1="28" y1="56" x2="42" y2="56"/></svg>
    <h3>Excepteur Sint<br>Occaecat</h3>
    <p>Excepteur sint occaecat cupidatat non proident, sunt in culpa qui officia deserunt error sit..</p>
  </article>
  <article class="card" style="left:798px">
    <svg width="64" height="64" viewBox="0 0 64 64" fill="none" stroke="var(--sky-btn)" stroke-width="2"><path d="M32 4l26 15v26L32 60 6 45V19z"/><path d="M14 24l18 10 18-10-18-10z"/><path d="M14 32l18 10 18-10"/><path d="M14 40l18 10 18-10"/></svg>
    <h3>Excepteur Sint<br>Occaecat</h3>
    <p>Excepteur sint occaecat cupidatat non proident, sunt in culpa qui officia deserunt error sit..</p>
  </article>
</section>

<section>
  <div class="placeholder" style="left:90px;top:1850px;width:450px;height:430px;border-radius:50%/40%;background:radial-gradient(circle,#dfe8ef,#f3f6f8)" role="img" aria-label="Isometric illustration of a laptop, servers and analytics tiles showing the product architecture"></div>
  <h2 class="sec-title" style="left:616px;top:1870px">Our <b>Product</b></h2>
  <p class="body-text" style="left:616px;top:1935px;width:512px">Sed ut perspiciatis unde omnis iste natus error sit voluptatem accusantium doloremque laudantium, totam rem aperiam, eaque ipsa quae ab illo inventore veritatis et quasi architecto beatae vitae dicta sunt explicabo. Nemo enim ipsam voluptatem quia voluptas sit aspernatur aut odit aut fugit, sed quia consequuntur magni dolores eos qui ratione voluptatem sequi nesciunt. Neque porro quisquam est, qui dolorem ipsum quia dolor sit amet, consecteturadipisci velit.</p>
  <a class="btn small-btn" style="left:616px;top:2160px">Learn More</a>
</section>

<svg class="abs" style="left:0;top:2250px" width="1200" height="680" viewBox="0 0 1200 680">
  <path d="M0,120 L600,50 C820,20 1010,-20 1110,40 C1180,80 1200,130 1200,200 L1200,530 L700,610 C500,650 200,670 60,660 C20,655 0,630 0,610 Z" fill="var(--sky-pale)"/>
  <path d="M0,112 L600,48 L560,62 L0,130 Z" fill="var(--teal-2)"/>
  <path d="M670,592 L1200,532 L1200,562 L700,602 Z" fill="var(--teal-2)"/>
</svg>

<section>
  <h2 class="sec-title center" style="top:2378px">Client <b>Testimonials</b></h2>
  <div class="quote-mark">“</div>
  <p class="quote">“ Duis aute irure dolor in reprehenderit in voluptate velit esse cillum dolore eu fugiat nulla pariatur. Excepteur sint occaecat cupidatat non proident, sunt in culpa qui officia deserunt mollit anim id est laborum."</p>
  <div class="person"><strong>Name Heading</strong><span>Company Name</span></div>
  <svg class="abs" style="left:72px;top:2590px" width="20" height="30" viewBox="0 0 20 30"><path d="M16 2L4 15l12 13" fill="none" stroke="#333" stroke-width="2.5"/></svg>
  <svg class="abs" style="left:1108px;top:2590px" width="20" height="30" viewBox="0 0 20 30"><path d="M4 2l12 13L4 28" fill="none" stroke="var(--teal)" stroke-width="2.5"/></svg>
</section>

<section>
  <h2 class="sec-title center" style="top:2952px">Latest <b>News</b></h2>
  <article class="news" style="left:74px">
    <div class="thumb" style="background:linear-gradient(135deg,#1a2a45,#0d1524 60%,#3a1e22)" role="img" aria-label="Photo of monitors showing code in a dark office"></div>
    <h3>Duis aute irure dolor in reprehenderit</h3>
    <p>Excepteur sint occaecat cupidatat non proident, sunt in culpa qui officia de serunt error sit..</p>
  </article>
  <article class="news" style="left:436px">
    <div class="thumb" style="background:linear-gradient(135deg,#2a1f5a,#0f1838 60%,#1b3a6a)" role="img" aria-label="Photo of a technician with a laptop in a server aisle"></div>
    <h3>Duis aute irure dolor in reprehenderit</h3>
    <p>Excepteur sint occaecat cupidatat non proident, sunt in culpa qui officia de serunt error sit..</p>
  </article>
  <article class="news" style="left:798px">
    <div class="thumb" style="background:linear-gradient(135deg,#0c2440,#1c3550 50%,#5a3418)" role="img" aria-label="Close-up photo of colourful lines of code on a screen"></div>
    <h3>Duis aute irure dolor in reprehenderit</h3>
    <p>Excepteur sint occaecat cupidatat non proident, sunt in culpa qui officia de serunt error sit..</p>
  </article>
  <svg class="abs" style="left:42px;top:3218px" width="18" height="28" viewBox="0 0 18 28"><path d="M15 2L4 14l11 12" fill="none" stroke="#333" stroke-width="2.5"/></svg>
  <svg class="abs" style="left:1140px;top:3218px" width="18" height="28" viewBox="0 0 18 28"><path d="M3 2l11 12L3 26" fill="none" stroke="#333" stroke-width="2.5"/></svg>
</section>

<svg class="abs" style="left:0;top:3480px" width="1200" height="76" viewBox="0 0 1200 76">
  <polygon points="0,35 700,60 1200,10 1200,76 0,76" fill="#1f4fa3"/>
  <polygon points="165,0 1200,28 1200,76 165,40" fill="var(--teal-2)"/>
  <polygon points="780,28 1200,0 1200,50" fill="#c7e6f5"/>
</svg>

<footer class="footer">
  <h2 class="subscribe">Subscribe <b>Newsletter</b></h2>
  <div class="email">Enter Email Address</div>
  <a class="btn sub-btn">Subscribe</a>
  <div class="rule"></div>
  <div class="f-brand"><span class="brand-mark"></span><span class="brand-name" style="color:var(--white)">QR.KA Horizon</span></div>
  <p class="copy">Copyright © 2025 Company Name<br>All Rights Reserved. <a>Impressum</a></p>
  <div class="socials"><span><i></i>Friendlo</span><span><i></i>Chirpa</span><span><i></i>Pixlo</span><span><i></i>Linkwork</span><span><i></i>Streamo</span></div>
  <div class="f-col" style="left:342px"><h4>Products and Services</h4><a>Sed ut perspiciatis</a><a>Unde omnis iste natus</a><a>Error sit voluptatem</a><a>Accusantiu</a></div>
  <div class="f-col" style="left:643px"><h4>Resources</h4><a>Sed ut perspiciatis</a><a>Unde omnis iste natus</a><a>Error sit voluptatem</a><a>Accusantiu</a></div>
  <div class="f-col" style="left:896px"><h4>Customer Support</h4><a>Sed ut perspiciatis</a><a>Unde omnis iste natus</a><a>Error sit voluptatem</a><a>Accusantiu</a></div>
</footer>

</div>
</body>
</html>
```